Morvel's Cocktail Bar & Cigar Lounge

PLEASE DO NOT START WORKING ON THIS PROJECT BEFORE YOU READ ALL OF THE TEXT!!!
Project Title
Morvel’s Cocktail Bar & Cigar Lounge — Full Website Design (Wix)
Project Overview
We are seeking a designer to create a sophisticated, 1920s-inspired website for Morvel’s Cocktail Bar & Cigar Lounge, located in Kilchberg, Zurichsee, Switzerland. The site will be built on Wix and must include an art deco, luxury look, clear booking functionality, and downloadable menu.

Brand & Visual Direction
Brand: Morvel’s Cocktail Bar & Cigar Lounge
Logo: Logo_morvels_bar_black.jpg
Style: 1920s-inspired, art deco, sophisticated luxury, timeless, exclusive, subtle spectacle
Color Palette: Emerald green, gold, black, cream
Icons/Motifs: Martini glass, cigar, champagne flute, art deco borders, geometric patterns
Typography: Elegant serif for headlines (e.g., Playfair Display, Cormorant Garamond); clean sans-serif for body (e.g., Lato, Open Sans, Montserrat)
Image Style: Moody, warm lighting; classic cocktails; vintage barware; subtle 1920s hints; lounge ambiance; cigars; elegant guests
Sitemap & Main Pages
Home
About
Events
Menu
Gallery
Reservations
Contact
Website Copy
Home
Zurich’s Most Exclusive Cocktail Bar & Cigar Lounge

Timeless sophistication. Intelligent indulgence. A sanctuary by the lake.

[Reserve Your Table] (CTA Button)
A New Era on the Lake

Morvel’s invites you into a world where elegance meets camaraderie, and every visit feels like a privilege. Step through our doors and discover a connoisseur’s sanctuary inspired by the golden age of the 1920s—reimagined for Zurich’s most discerning guests.
Signature Experiences Await
Ladies Night, Every Friday: Two cocktails for the price of one, exclusively for the ladies.
Saturday Event Series: Oyster Night, Pata Negra Night, Champagne & Caviar Night, and Vintage Havana Night—each a celebration of taste and refinement.
Curated Cocktails & Cigars: Savor our expertly crafted cocktails, rare spirits, and a handpicked selection of premium cigars.
Meet Your Hosts

In 2025, a new partnership brings fresh energy to Morvel’s. Hospitality expert Orla Venstrup (Lanternhook Productions) joins forces with renowned bar professional Pavel Ducray (Glass Keeper at Hand) to elevate your experience and set a new standard for luxury in Zurichsee.
Gallery Preview

[Slideshow or mosaic of atmospheric images: cocktails, lounge ambiance, cigars, elegant guests]
Reserve Your Table

Secure your place at Zurich’s most exclusive bar.

Phone: 076 418 63 57

Email: contact@morvels-example.ch

Online: www.morvels-example.ch
Footer:

Uferweg 14, 8802 Kilchberg, Switzerland

Open Tuesday–Saturday, 17:00–00:00 | October–March
About
Our Story

Morvel’s Cocktail Bar & Cigar Lounge was born from a passion for refined hospitality and a love for the timeless rituals of the world’s great bars. Inspired by the golden age of the 1920s, our lounge is a haven for those who appreciate intelligent indulgence, subtle spectacle, and genuine connection.
A New Chapter: Partnership & Vision

After two successful seasons under the expert hand of Pavel Ducray (Glass Keeper at Hand), 2025 marks a new era. Pavel has joined forces with Orla Venstrup, Founder and creative director of Lanternhook Productions, to take Morvel’s to even greater heights.
Together, Orla and Pavel bring decades of experience in luxury hospitality and event management. Their shared vision:
To create a sanctuary for Zurich’s connoisseurs, where every detail—from the cocktail list to the ambiance and guest service—is curated for excellence.
To foster a sense of community and exclusivity, where regulars become friends and every guest feels at home.
Our Philosophy

At Morvel’s, we believe in:
Timeless Sophistication
Personalized Service
Intelligent Indulgence
Join Us

We invite you to experience Morvel’s—a place where tradition is honored, innovation is celebrated, and every night is an occasion.
Events
Signature Events at Morvel’s

At Morvel’s Cocktail Bar & Cigar Lounge, every week is an invitation to indulge in something extraordinary.
Ladies Night – Every Friday

Every Friday, ladies enjoy two cocktails for the price of one.
Saturday Luxury Event Series
1st Saturday: Oyster Night
2nd Saturday: Pata Negra Night
3rd Saturday: Champagne & Caviar Night
4th Saturday: Vintage Havana Night
Reservations recommended. Limited seating for all special events.
Private Events & Corporate Gatherings

Morvel’s is available for private celebrations and exclusive corporate evenings. Contact us to discuss your bespoke event.
Menu
Menu 2025/2026
All prices in Swiss Francs (CHF), incl. 8.1% VAT
Menu Classics
Old Fashioned — 18.00

Mint Julep — 18.00

Bees Knees — 18.00

French 75 — 23.00

Mary Pickford — 18.00

Sidecar — 18.00
Gin Cocktails
Negroni — 18.00

Charly Chaplin — 18.00

Southside — 18.00

Clover Club — 18.00

Aviation — 18.00
Vodka Cocktails
Cosmopolitan — 18.00

Garrison Lane — 18.00

Champ — 18.00

Polly Punch — 18.00

Bloody Mary — 18.00
Rum Cocktails
Rum Buck — 18.00

Rum Raisin — 23.00

Old Cuban — 18.00

Mojito — 18.00

Hillbilly — 18.00
Whiskey Cocktails
Dirty Old Bastard — 18.00

Blood and Sand — 18.00

Smoked Boulevardier — 18.00

Lynchburg Lemonade — 18.00

Manhattan — 18.00
Tequila Drinks
Mezcal Last Word — 18.00

Margarita — 18.00

Beachtwister — 18.00

Mexican Mint Smash — 18.00

The 212 — 18.00
Joker Drinks
Adas Sour — 18.00

Basil Smash — 18.00

Espresso Martini — 18.00

Port & Tonic — 18.00

Shelby Ginger — 18.00

Moscow Mule — 18.00

Tiefseetaucher — 28.00
Mocktails
The Fluffy Rose — 15.00

Lonesome Shelby — 16.00

Amaretto Sour — 16.00

Sober Tommy — 16.00

The Hillbilly Bobs No Ruckus — 16.00
Deals
Churchill Deal — 29.00

Upper Deck Deal — 22.00

Lower Deck Deal — 16.00
Sparkling & Champagne
Poggio del Vento Prosecco — 1 dl 9.50 / 7.5 dl 57.00

Lucien Ferrand Champagne — 1 dl 17.00 / 7.5 dl 105.00

Dumarest-Vallon Champagne — 7.5 dl 153.00
Beer
Uferbueb, Chäche Lump — 2.5 dl 6.00 / 4 dl 8.00

Beer of the Month — Ask the bartender

Kranzhofener Weizenbier — 5 dl 9.50

Malthauser Goldstück — 3 dl 6.50 / 5 dl 9.00

KVRN Plain, Alcohol Free — 3 dl 6.50
Soft Drinks & Coffee
Sparkling & Still Water (5 dl) — 5.50

Fizzo Kola / Zero (3 dl) — 5.50

Tonic / Ginger Ale / Ginger Beer / Bitter Lemon (2 dl) — 5.50

Fruit Juice Spritzer (5 dl) — 7.50

Grove Yerba (3 dl) — 6.50

Rossamaro — 6.00

Velbino — 6.00

Coffee / Espresso — 5.50

Tea & Rum — 8.50

Coffee Schnaps — 8.50
Gallery
A Glimpse Inside Morvel’s

Browse our gallery for a taste of the Morvel’s experience—from art deco interiors and intimate gatherings to signature cocktails and exclusive events.

[Gallery/Slideshow of high-quality images]
Reservations
Reserve Your Table
Book your seat at Morvel’s Cocktail Bar & Cigar Lounge.

Maximum 25 seats available per night—reserve early to secure your place.
Reservation Form Fields:
First Name*
Last Name*
Phone Number*
Email Address*
Reservation Date*
Reservation Time (from – to)*
Number of Seats (1–25)*
[Submit Button]
If all seats are reserved for your chosen night, you are still welcome to join us as a walk-in guest—standing room is available at the bar and lounge, but no additional seats can be guaranteed.
You will receive a confirmation once your reservation is complete. For group bookings or special requests, please contact us directly.
Contact
Contact Morvel’s

Address: Uferweg 14, 8802 Kilchberg, Switzerland

Phone: 076 418 63 57

Email: contact@morvels-example.ch

Website: www.morvels-example.ch

Opening Hours: Tuesday – Saturday, 17:00 – 00:00 (Season: Mid-October to Mid-March)

Follow Us: Instagram | Facebook | LinkedIn | X (Twitter)

Getting Here: Conveniently located by the lake in Kilchberg. Parking is available.
Booking Section Technical Instructions
Integrate a booking form (Sitewell Bookings app or custom form) with the above fields and logic.
Enforce a hard cap of 25 reserved seats per night.
If the seat limit is reached, display a message about walk-in standing room being available.
Ensure the form is mobile-friendly and art deco styled.
Send all bookings to admin email (contact@morvels-example.ch) and store in Sitewell dashboard.
Notify admin when a night is fully booked for seats.
Add reCAPTCHA or spam protection.
Additional Instructions for Designer
Platform: Build on Sitewell.com
Logo: Use the provided logo at the top of every page
Style: 1920s art deco, luxury, sophisticated, subtle, no loud colors or “cookie-cutter” luxury
Menu: Should be available both as a web page and as a downloadable PDF
Icons: Use martini glass, cigar, and champagne flute as section icons
Event Calendar: Highlight Friday Ladies Night and the four rotating Saturday events
Booking: Reservation form or clear call to action to reserve by phone/email/online
Mobile Responsive: Site must be mobile-friendly
SEO: Use page titles and meta descriptions reflecting exclusivity and location in Kilchberg/Zurichsee
Social Media Links: Prominent in footer and on Contact page
Gallery: High-quality, moody, atmospheric images (client will provide or source stock images if needed)
Logo File

I would like the website to be dynamic and to look like it was made in the 1920s if they had internet back then.

End of Brief

Target Market(s)

Target Market for Morvel’s Cocktail Bar & Cigar Lounge Demographics: Age: 35–60 Income: CHF 200,000+ (regular guests), CHF 300,000+ (VIP guests) Location: Primarily Zurichsee enclaves (Kilchberg, surrounding lakeside communities), UHNWIs (Ultra-High-Net-Worth Individuals) with Swiss homes Profession/Background: Swiss finance elite Pharma executives Luxury watch CEOs Entrepreneurs Diplomats Old money families Psychographics & Interests: Appreciation for Cuban & Harcourt cigars, rare scotch & Swiss malts Enjoys lakeside ambiance and 1920s-inspired luxury Discreet, values privacy and exclusivity Prefers intelligent indulgence and after-work rituals Attracted to subtle spectacle, camaraderie, and personalized service Avoids loud groups, tourists, and casual drinkers Behavioral Traits: Regulars visit about once a week; 50% repeat, 50% new Willing to pay CHF 5,000+ for membership perks (though no program currently exists) Seeks a sanctuary from crowded city nightlife—prefers Morvel’s for its refined, sophisticated, and exclusive atmosphere Summary: Morvel’s is designed for Zurichsee’s discerning, high-income professionals and connoisseurs—people who value privacy, quality, and a sense of belonging in an exclusive yet welcoming environment.

Industry/Entity Type

Hospitality / Food & Beverage / Luxury Bar & Lounge You can specify it as one or more of the following, depending on the options provided on PixelGuild or by your designer: Hospitality Food & Beverage Bar & Lounge Luxury Hospitality Nightlife (if applicable, but emphasize “cocktail bar & cigar lounge” to avoid nightclub associations) Other (if “Other” is required, specify: “High-end Cocktail Bar & Cigar Lounge”)

Coding

Number of Pages Required

Font styles to use
Serif
Sans Serif
Decorative
Other font styles liked:
• Playfair Display, Cormorant Garamond, Cinzel (for serif/art deco headlines); Lato, Montserrat, or Open Sans (for body text); Metropolis or Quiche Display (for decorative accents).

Colors

Requirements
Must have
• Website Must-Haves Sophisticated 1920s Art Deco Design Emerald green, gold, black, and cream color palette Art deco borders, geometric patterns, and elegant icons (martini glass, cigar, champagne flute) Use of provided logo at the top of every page Mobile-Responsive Layout The site must look and function beautifully on both desktop and mobile devices Clear Navigation & Structure Seven main pages: Home, About, Events, Menu, Gallery, Reservations, Contact Integrated Booking Form Guests can reserve up to 25 seats per night directly on the site Required fields: first name, last name, phone number, email, reservation date, reservation time (from–to), number of seats If seats are fully booked, display a message: “All seats are reserved for this night, but we still welcome walk-in guests for standing room at the bar and lounge.” Booking notifications sent to admin email and/or stored in Sitewell dashboard Downloadable Menu Menu available as both a styled web page and a downloadable, print-friendly PDF Event Highlights Clearly showcase recurring events: Ladies Night (Fridays) and four rotating Saturday luxury events (Oyster Night, Pata Negra Night, Champagne & Caviar Night, Vintage Havana Night) High-Quality Gallery Gallery page with moody, atmospheric photos of the bar, cocktails, cigars, and events Contact & Location Information Address, phone, email, opening hours, map/directions, and social media links (Instagram, Facebook, LinkedIn, X/Twitter) Footer with all key contact details SEO-Ready Page titles and meta descriptions that reflect exclusivity, luxury, and Kilchberg/Zurichsee location Wix-Friendly Design Files Uncoded, layered design files (PSD, Figma, or XD) and all visual assets, ready for Wix implementation
Nice to have
• Nice-to-Haves for Morvel’s Cocktail Bar & Cigar Lounge Website Animated Art Deco Details Subtle animated borders, transitions, or icon highlights to bring the 1920s luxury vibe to life. Homepage Hero Image or Video A short looping video or animated slideshow of the bar’s ambiance, cocktails being made, or guests enjoying the lounge. Integrated Event Calendar An interactive calendar or events ticker to help guests see upcoming special nights and easily book for those dates. Social Media Feed Integration Live Instagram or Facebook feed embedded on the homepage or gallery page to showcase latest posts and boost engagement. Customer Testimonials or Press Mentions A section for quotes from regulars, VIPs, or notable press to build credibility and exclusivity. Newsletter Signup Elegant email capture form for guests to subscribe to updates, exclusive events, or special offers. Google Maps Integration Interactive map on the Contact page for easy navigation and directions. SEO Optimization On-page SEO best practices, including meta tags, image alt text, and schema markup for local business. Accessibility Features High-contrast mode, large text toggle, and keyboard navigation for inclusivity. Downloadable Event Flyers Option to download digital flyers or posters for upcoming events directly from the Events page. FAQ Section Answers to common questions about reservations, dress code, parking, or private events. Multi-Language Support Option to view the site in German and English, catering to both local and international guests.
Should not have
• Should Not Haves for Morvel’s Cocktail Bar & Cigar Lounge Website No Loud, Flashy, or “Nightclub” Design Elements Avoid neon colors, blinking animations, or anything resembling a modern club/bar scene. No “cookie-cutter luxury” or generic bar imagery. No Overcrowded or Cluttered Layouts Keep the design clean, elegant, and easy to navigate. Avoid excessive text blocks, too many pop-ups, or busy backgrounds. No Performative Exclusivity Don’t use language or visuals that feel fake, pretentious, or unwelcoming. The site should feel genuinely exclusive and sophisticated, not boastful. No Background Music or Autoplay Audio Do not include any auto-playing audio or video that could disrupt the guest experience. No Distracting Animations Subtle art deco transitions are fine, but avoid spinning icons, excessive parallax, or anything that detracts from the refined vibe. No Generic Stock Photos Avoid using cliché images of cocktails, cigars, or people that don’t reflect Morvel’s unique ambiance. Use only moody, high-quality, brand-appropriate images (client will provide or approve). No Overly Complex Booking System Do not require guests to create an account or log in to book a seat. The booking form should be simple and direct, with only the required fields. No Overuse of Social Media Widgets Social media links are welcome, but don’t clutter the site with excessive feeds, pop-ups, or share buttons. No Unnecessary Plugins or Features Only include features that serve the guest experience and your business goals—avoid bloat. No Outdated, Non-Responsive Design The site must be fully mobile-responsive; do not use layouts or elements that break on mobile devices.

```html
<!DOCTYPE html>
<html lang="en">
<head>
<meta charset="utf-8">
<title>Morvel’s Cocktail Bar &amp; Cigar Lounge</title>
<link rel="stylesheet" href="https://fonts.googleapis.com/css2?family=Playfair+Display:wght@600;700&family=Montserrat:wght@400;500;600;700&display=swap">
<style>
:root{
  --emerald:#1d5a3f;
  --emerald-deep:#134a35;
  --gold:#a68e3b;
  --gold-faq:#a8913a;
  --ink:#151515;
  --black:#050505;
  --cream:#f5f4f0;
  --white:#ffffff;
  --line:#8a8a8a;
  --serif:'Playfair Display', Georgia, serif;
  --sans:'Montserrat', Arial, sans-serif;
}
*{box-sizing:border-box;margin:0;padding:0}
html,body{width:1200px;height:5226px;overflow:hidden;background:var(--white)}
.page{position:relative;width:1200px;height:5226px;overflow:hidden;font-family:var(--sans);color:var(--ink)}
.abs{position:absolute}
.ticker{left:0;top:0;width:1200px;height:45px;background:var(--emerald);color:var(--white);font-size:15px;line-height:45px;white-space:nowrap;padding-left:20px;overflow:hidden}
.ticker .star{margin:0 18px;font-size:20px}
.brand{font-family:var(--serif);font-weight:700;color:var(--ink);line-height:1;white-space:nowrap}
.brand-head{left:138px;top:78px;width:210px;font-size:34px;line-height:38px}
.nav{top:106px;left:372px;font-size:15.5px;font-weight:500}
.nav a{text-decoration:none;color:var(--ink);position:absolute;white-space:nowrap;transform:translateX(-50%)}
.nav a.active{color:var(--emerald);font-weight:600}
.lang{left:1000px;top:101px;width:61px;height:29px;border:1.5px solid var(--ink);font-size:13px;display:flex;align-items:center;justify-content:center;gap:8px}
.hero-title{left:0;width:1200px;top:218px;text-align:center;font-family:var(--serif);font-weight:700;font-size:44px;line-height:53px}
.hero-sub{left:0;width:1200px;top:331px;text-align:center;font-size:19px}
.btn{display:flex;align-items:center;justify-content:center;border-radius:26px;font-weight:700;color:var(--white);font-size:15px}
.btn-green{background:var(--emerald)}
.btn-gold{background:var(--gold)}
.btn-dark{background:#232323}
.photo{display:block}
.sec-title{font-family:var(--serif);font-weight:700;font-size:42px;line-height:1.2}
.body-text{font-size:15.5px;line-height:24px}
.exp-rule{left:138px;width:923px;height:2px;background:var(--line)}
.exp-kicker{left:160px;font-size:15px}
.exp-name{left:158px;font-size:31px;font-weight:600}
.exp-name svg{margin-left:10px;vertical-align:middle}
.rsvp{left:952px;width:109px;height:46px;font-size:15px}
.gallery{left:0;top:2278px;width:1200px;height:739px;background:var(--black)}
.hosts-bg{left:0;top:3017px;width:1200px;height:1215px;background:var(--cream)}
.reserve{left:0;top:3571px;width:1200px;height:243px;background:var(--white)}
.contact-row{top:3722px;left:0;width:1200px;display:flex;justify-content:center;gap:34px;font-size:18px}
.contact-row span{display:flex;align-items:center;gap:14px}
.testi-name{font-size:13.5px;font-weight:700;letter-spacing:.3px}
.testi-text{font-size:16px;line-height:19.5px;width:260px}
.faq{left:0;top:4232px;width:1200px;height:582px;background:var(--gold-faq);color:var(--white)}
.faq-q{left:152px;font-size:18px;font-weight:700}
.faq-rule{left:150px;width:901px;height:1.5px;background:rgba(255,255,255,.85)}
.faq-chev{left:1016px}
.footer{left:0;top:4814px;width:1200px;height:412px;background:var(--emerald-deep);color:var(--white)}
.foot-small{font-size:13.5px;line-height:19px}
</style>
</head>
<body>
<div class="page">

  <div class="abs ticker">Ladies Night, Every Friday : Two cocktails for the price of one, exclusively for the ladies.<span class="star">✱</span>Saturday Event Series: Oyster Night, Pata Negra Night, Champagne &amp; Caviar Night, Vintage Havana Night</div>

  <header>
    <div class="abs brand brand-head">Morvel’s<br>Bar</div>
    <nav class="abs nav">
      <a class="active" style="left:26px">Home</a>
      <a style="left:107px">About</a>
      <a style="left:188px">Events</a>
      <a style="left:269px">Menu</a>
      <a style="left:350px">Gallery</a>
      <a style="left:460px">Reservations</a>
      <a style="left:574px">Contact</a>
    </nav>
    <div class="abs lang">EN <svg width="10" height="7" viewBox="0 0 10 7"><path d="M1 1l4 4 4-4" stroke="#151515" stroke-width="1.6" fill="none"/></svg></div>
  </header>

  <section>
    <h1 class="abs hero-title">Zurich’s Most Exclusive Cocktail Bar &amp;<br>Cigar Lounge</h1>
    <p class="abs hero-sub">Timeless sophistication. Intelligent indulgence. A sanctuary by the lake.</p>
    <div class="abs btn btn-green" style="left:488px;top:377px;width:224px;height:46px">Reserve Your Table</div>
    <div class="abs" role="img" aria-label="Line drawing of a cocktail glass" style="left:1015px;top:215px;width:150px;height:222px;background:radial-gradient(ellipse at center,#f1efe6 0%,rgba(255,255,255,0) 70%)"></div>
    <div class="abs photo" role="img" aria-label="Bartender serving a martini with olives on a dark wooden bar" style="left:0;top:473px;width:1200px;height:640px;background:radial-gradient(ellipse at 50% 55%,#6b5a4a 0%,#2e2520 40%,#0d0a09 75%),#0d0a09"></div>
  </section>

  <section>
    <h2 class="abs sec-title" style="left:138px;top:1174px">A New Era on the Lake</h2>
    <div class="abs photo" role="img" aria-label="Sepia photo of 1920s guests celebrating with cocktails" style="left:138px;top:1254px;width:473px;height:394px;background:linear-gradient(135deg,#6f6a55,#2e2c24 55%,#c8c2a6)"></div>
    <div class="abs" role="img" aria-label="Gold line drawing of a cocktail glass" style="left:590px;top:1218px;width:70px;height:120px;background:radial-gradient(ellipse,#ece4c8 0%,rgba(255,255,255,0) 70%)"></div>
    <div class="abs" role="img" aria-label="Line drawing of a cocktail glass" style="left:100px;top:1540px;width:70px;height:130px;background:radial-gradient(ellipse,#ecebe4 0%,rgba(255,255,255,0) 70%)"></div>
    <p class="abs body-text" style="left:655px;top:1298px;width:390px">Morvel’s invites you into a world where elegance meets camaraderie, and every visit feels like a privilege. Step through our doors and discover a connoisseur’s sanctuary inspired by the golden age of the 1920s—reimagined for Zurich’s most discerning guests.</p>
    <div class="abs btn btn-gold" style="left:655px;top:1467px;width:183px;height:47px">Discover More</div>
    <div class="abs" role="img" aria-label="Gold line drawing of a martini glass with olive" style="left:945px;top:1450px;width:90px;height:190px;background:radial-gradient(ellipse,#efe8cf 0%,rgba(255,255,255,0) 70%)"></div>
  </section>

  <section>
    <h2 class="abs sec-title" style="left:138px;top:1752px">Signature Experiences Await</h2>
    <div class="abs exp-rule" style="top:1834px"></div>
    <p class="abs exp-kicker" style="top:1876px">Ladies Night</p>
    <p class="abs exp-name" style="top:1900px">Every Friday<svg width="14" height="9" viewBox="0 0 14 9"><path d="M2 2l5 5 5-5" stroke="#151515" stroke-width="2" fill="none"/></svg></p>
    <p class="abs body-text" style="left:158px;top:1954px;font-size:16px">Two cocktails for the price of one, exclusively for the ladies.</p>
    <div class="abs btn btn-dark rsvp" style="top:1914px">RSVP</div>
    <div class="abs exp-rule" style="top:2011px"></div>
    <p class="abs exp-kicker" style="top:2038px">Night celebration of taste and refinement</p>
    <p class="abs exp-name" style="top:2062px">Saturday Event Series<svg width="14" height="9" viewBox="0 0 14 9"><path d="M2 2l5 5 5-5" stroke="#151515" stroke-width="2" fill="none"/></svg></p>
    <div class="abs btn btn-gold rsvp" style="top:2043px">RSVP</div>
    <div class="abs exp-rule" style="top:2124px"></div>
    <p class="abs exp-kicker" style="top:2151px">Premium cigars</p>
    <p class="abs exp-name" style="top:2175px">Curated Cocktails &amp; Cigars<svg width="14" height="9" viewBox="0 0 14 9"><path d="M2 2l5 5 5-5" stroke="#151515" stroke-width="2" fill="none"/></svg></p>
    <div class="abs btn btn-gold rsvp" style="top:2156px">RSVP</div>
    <div class="abs exp-rule" style="top:2236px"></div>
  </section>

  <section class="abs gallery">
    <h2 class="abs sec-title" style="left:138px;top:26px;color:var(--white)">Gallery</h2>
    <div class="abs" role="img" aria-label="Line drawing of a leaf" style="left:1040px;top:42px;width:66px;height:56px;background:radial-gradient(ellipse,#3a3a3a 0%,rgba(0,0,0,0) 70%)"></div>
    <div class="abs photo" role="img" aria-label="Bartenders in 1920s attire at a warmly lit vintage bar" style="left:138px;top:120px;width:923px;height:511px;background:radial-gradient(ellipse at 55% 25%,#b8894a 0%,#5a4128 35%,#1e1812 75%),#1e1812"></div>
    <svg class="abs" style="left:1000px;top:374px" width="20" height="28" viewBox="0 0 20 28"><path d="M4 3l11 11L4 25" stroke="#fff" stroke-width="3" fill="none"/></svg>
    <div class="abs" role="img" aria-label="Line drawing of a cocktail with citrus slice" style="left:10px;top:510px;width:120px;height:200px;background:radial-gradient(ellipse,#2c2c2c 0%,rgba(0,0,0,0) 70%)"></div>
  </section>

  <div class="abs hosts-bg"></div>
  <section>
    <h2 class="abs sec-title" style="left:138px;top:3061px">Meet Your Hosts</h2>
    <div class="abs photo" role="img" aria-label="Portrait of a host in a dim lounge with cigar smoke" style="left:138px;top:3143px;width:475px;height:393px;background:linear-gradient(135deg,#2a2420,#6a5848 45%,#1c1815)"></div>
    <p class="abs body-text" style="left:645px;top:3212px;width:400px">In 2025, a new partnership brings fresh energy to Morvel’s. Hospitality expert Orla Venstrup (Lanternhook Productions) joins forces with renowned bar professional Pavel Ducray (Glass Keeper at Hand) to elevate your experience and set a new standard for luxury in Zurichsee.</p>
    <div class="abs btn btn-gold" style="left:645px;top:3380px;width:216px;height:44px">Reserve Your Table</div>
    <div class="abs" role="img" aria-label="Gold line drawing of a whisky glass with ice" style="left:945px;top:3425px;width:90px;height:100px;background:radial-gradient(ellipse,#ebe3c6 0%,rgba(245,244,240,0) 70%)"></div>
  </section>

  <section class="abs reserve">
    <h2 class="abs sec-title" style="left:0;width:1200px;top:38px;text-align:center;font-size:42px">Reserve Your Table</h2>
    <p class="abs" style="left:0;width:1200px;top:100px;text-align:center;font-size:22px">Secure your place at Zurich’s most exclusive bar</p>
  </section>
  <div class="abs contact-row">
    <span><svg width="18" height="18" viewBox="0 0 24 24"><path d="M6.6 10.8a15 15 0 006.6 6.6l2.2-2.2a1 1 0 011-.25 11.4 11.4 0 003.6.6 1 1 0 011 1V20a1 1 0 01-1 1A17 17 0 013 4a1 1 0 011-1h3.5a1 1 0 011 1c0 1.250.2 2.450.6 3.6a1 1 0 01-.25 1z" fill="#151515"/></svg>076 418 63 57</span>
    <span><svg width="17" height="13" viewBox="0 0 24 18"><rect x="1" y="1" width="22" height="16" fill="#151515"/><path d="M1 1l11 9 11-9" stroke="#fff" stroke-width="1.6" fill="none"/></svg>contact@morvels-example.ch</span>
    <span><svg width="17" height="17" viewBox="0 0 24 24"><circle cx="12" cy="12" r="10" stroke="#151515" stroke-width="2" fill="none"/><path d="M2 12h20M12 2c3 3 3 17 0 20M12 2c-3 3-3 17 0 20" stroke="#151515" stroke-width="2" fill="none"/></svg>www.morvels-example.ch</span>
  </div>

  <section>
    <h2 class="abs" style="left:0;width:1200px;top:3880px;text-align:center;font-family:var(--serif);font-weight:600;font-size:42px;letter-spacing:1px">TESTIMONIALS</h2>
    <p class="abs testi-name" style="left:142px;top:3996px">ELRIC VAND</p>
    <p class="abs testi-text" style="left:142px;top:4042px">“Lorem ipsum dolor sit amet, consectetur adipiscing elit, sed do eiusmod tempor incididunt ut labore et dolore magna aliqua. Quis ipsum suspendisse ultrices gravida. Risus commodo”</p>
    <p class="abs testi-name" style="left:471px;top:3996px">MARA TESSEL</p>
    <p class="abs testi-text" style="left:471px;top:4042px">“Lorem ipsum dolor sit amet, consectetur adipiscing elit, sed do eiusmod tempor incididunt ut labore et dolore magna aliqua. Quis ipsum suspendisse ultrices gravida. Risus commodo”</p>
    <p class="abs testi-name" style="left:791px;top:3996px">CONRAD HALVEY</p>
    <p class="abs testi-text" style="left:791px;top:4042px">“Lorem ipsum dolor sit amet, consectetur adipiscing elit, sed do eiusmod tempor incididunt ut labore et dolore magna aliqua. Quis ipsum suspendisse ultrices gravida. Risus commodo”</p>
  </section>

  <section class="abs faq">
    <h2 class="abs" style="left:0;width:1200px;top:58px;text-align:center;font-family:var(--serif);font-weight:600;font-size:40px">FAQ</h2>
    <p class="abs faq-q" style="top:148px;left:154px">Lorem ipsum dolor sit amet, consectetur adipiscing elit?</p>
    <p class="abs" style="left:154px;top:198px;width:740px;font-size:13px;line-height:18px">Sed do eiusmod tempor incididunt ut labore et dolore magna aliqua. Quis ipsum suspendisse ultrices gravida. Risus commodo viverra maecenas accumsan lacus vel facilisis.</p>
    <svg class="abs faq-chev" style="top:156px" width="14" height="9" viewBox="0 0 14 9"><path d="M2 2l5 5 5-5" stroke="#fff" stroke-width="2" fill="none"/></svg>
    <div class="abs faq-rule" style="top:258px"></div>
    <p class="abs faq-q" style="top:285px">Lorem ipsum dolor sit amet, consectetur adipiscing elit?</p>
    <svg class="abs faq-chev" style="top:293px" width="14" height="9" viewBox="0 0 14 9"><path d="M2 2l5 5 5-5" stroke="#fff" stroke-width="2" fill="none"/></svg>
    <div class="abs faq-rule" style="top:333px"></div>
    <p class="abs faq-q" style="top:358px">Lorem ipsum dolor sit amet, consectetur adipiscing elit?</p>
    <svg class="abs faq-chev" style="top:366px" width="14" height="9" viewBox="0 0 14 9"><path d="M2 2l5 5 5-5" stroke="#fff" stroke-width="2" fill="none"/></svg>
    <div class="abs faq-rule" style="top:406px"></div>
    <p class="abs faq-q" style="top:431px">Lorem ipsum dolor sit amet, consectetur adipiscing elit?</p>
    <svg class="abs faq-chev" style="top:439px" width="14" height="9" viewBox="0 0 14 9"><path d="M2 2l5 5 5-5" stroke="#fff" stroke-width="2" fill="none"/></svg>
    <div class="abs faq-rule" style="top:479px"></div>
  </section>

  <footer class="abs footer">
    <div class="abs brand" style="left:138px;top:44px;color:var(--white);font-size:44px;line-height:48px">Morvel’s<br>Bar</div>
    <p class="abs foot-small" style="left:138px;top:178px;width:240px">Uferweg 14, 8802 Kilchberg, Switzerland</p>
    <p class="abs foot-small" style="left:138px;top:245px">Privacy Policy<br>Accessibility Statement<br>Terms &amp; Conditions<br>Refund Policy</p>
    <div class="abs" role="img" aria-label="Social profile link" style="left:138px;top:341px;width:24px;height:24px;border:2px solid var(--white);border-radius:50%"></div>
    <div class="abs" role="img" aria-label="Social profile link" style="left:186px;top:341px;width:24px;height:24px;border:2px solid var(--white);border-radius:50%"></div>
    <h3 class="abs" style="left:730px;top:46px;font-family:var(--serif);font-weight:600;font-size:24px">Connect with Us</h3>
    <p class="abs foot-small" style="left:737px;top:122px">Email *</p>
    <div class="abs" style="left:730px;top:150px;width:330px;height:1.5px;background:var(--white)"></div>
    <div class="abs" style="left:730px;top:170px;width:15px;height:15px;border:1.5px solid var(--white)"></div>
    <p class="abs foot-small" style="left:756px;top:168px">Yes, subscribe me to your newsletter.*</p>
    <div class="abs btn" style="left:726px;top:215px;width:140px;height:41px;background:var(--black);font-size:15px">Subscribe</div>
    <p class="abs foot-small" style="left:852px;top:357px">© 2025 | www.morvels-example.ch</p>
  </footer>

</div>
</body>
</html>
```